Catalogue Design Project

We need a catalog design for a new private university called Redwell Institute Bayshore (see website www.rwi-bs.org). The catalog should be about 30 pages maximum and will include items such as General Information, Academic schedule, department descriptions, program descriptions, course descriptions, school policies, student services, admissions, San diego Lifestyle, etc.
I will provide the text but I need a professional design with regard to page layouts. I have provided some examples.
Ok, i posted the catalog content, just missing course descriptions.
Target Market(s)
Young Professionals, Foreign Students
Industry/Entity Type
University
Look and feel
Each slider illustrates characteristics of the customer's brand and the style your logo design should communicate.

```html
<!DOCTYPE html>
<html lang="en">
<head>
<meta charset="utf-8">
<title>University Policies – Redwell Institute</title>
<link href="https://fonts.googleapis.com/css2?family=Carlito:wght@400;700&display=swap" rel="stylesheet">
<style>
  :root {
    --navy: #1f4e79;
    --rule: #8fa9c4;
    --ink: #111111;
    --muted: #8a8a8a;
    --paper: #ffffff;
    --mark: #b7c4d2;
  }
  html, body { margin: 0; padding: 0; overflow: hidden; }
  body { width: 927px; height: 1200px; background: var(--paper); }
  .page {
    position: relative; width: 927px; height: 1200px; overflow: hidden;
    font-family: "Carlito", "Calibri", sans-serif; color: var(--ink);
  }
  .brand-mark {
    position: absolute; left: 60px; top: 34px; width: 156px; height: 34px;
    background: var(--mark); border-radius: 4px;
  }
  .header-visual {
    position: absolute; left: 680px; top: 0; width: 247px; height: 104px;
    background: linear-gradient(135deg, #ffffff 0%, #eef3f8 55%, #dde6ef 100%);
  }
  .header-band { position: absolute; left: 0; top: 100px; width: 927px; height: 46px; }
  .header-title {
    position: absolute; left: 602px; top: 104px; width: 325px; height: 40px;
    color: #fff; font-size: 30px; line-height: 40px; text-align: center; letter-spacing: 0.5px;
  }
  .page-title {
    position: absolute; left: 0; top: 160px; width: 927px; margin: 0;
    text-align: center; font-size: 25px; font-weight: 700;
  }
  .policy { position: absolute; left: 80px; width: 768px; }
  .policy h2 {
    margin: 0 0 2px; font-size: 19px; font-weight: 400; text-decoration: underline;
    text-underline-offset: 3px; line-height: 24px;
  }
  .policy p { margin: 0; font-size: 15.4px; line-height: 20px; text-align: justify; }
  .footer-rule { position: absolute; left: 0; top: 1153px; width: 927px; height: 2px; background: var(--rule); }
  .folio {
    position: absolute; right: 36px; top: 1170px; font-size: 14px;
    color: var(--muted); letter-spacing: 0.3px;
  }
</style>
</head>
<body>
<div class="page">
  <div class="brand-mark" role="img" aria-label="Institute emblem area"></div>
  <div class="header-visual" role="img" aria-label="Faint graduation cap illustration"></div>

  <svg class="header-band" viewBox="0 0 927 46" width="927" height="46" aria-hidden="true">
    <line x1="0" y1="6" x2="927" y2="6" stroke="#8fa9c4" stroke-width="2"/>
    <polygon points="590,6 927,6 927,44 602,44" fill="#1f4e79"/>
  </svg>
  <div class="header-title">UNIVERSITY POLICIES</div>

  <h1 class="page-title">University Policies</h1>

  <section class="policy" style="top:230px">
    <h2>Withdrawing from the University</h2>
    <p>A currently registered student may withdraw from the university at any time and receive any eligible tuition refund.&nbsp; A formal withdrawal form must be completed and submitted to the Office of the Registrar.&nbsp; Non-attendance or non-payment of tuition and fees will not constitute a withdrawal.&nbsp; Transcripts will not include any courses that were in progress and never completed.&nbsp; They will be listed as “DC” or dropped course.</p>
  </section>

  <section class="policy" style="top:386px">
    <h2>Probation and Dismissal</h2>
    <p>A graduate or certificate student whose fails any given course will be placed on academic probation.&nbsp; A student who subsequently fails a second course will be considered from dismissal from the university.&nbsp; Students can appeal a dismissal or failed grade within 2 weeks of the notice.&nbsp; The appeal must be in writing and delivered to the Admissions office.&nbsp; Students who are dismissed have the option of applying again after 2 quarters following the dismissal.</p>
  </section>

  <section class="policy" style="top:542px">
    <h2>Student Records</h2>
    <p>Redwell Institute Bayshore protects the confidentiality of all student educational records in accordance with state and federal laws.&nbsp; Student academic records are maintained by the Office of the Register and cannot be disclosed or release without written permission of the student.</p>
  </section>

  <section class="policy" style="top:656px">
    <h2>Academic Honesty</h2>
    <p>Students are expected to submit only original papers for all course assignments.&nbsp; Use of already documented language must be cited correctly according to APA standards.&nbsp; Any students that have been found to engage in plagirism can and will be dismissed from the university.&nbsp; Please contact an instructor or academic advisor for more information on academic dishonesty.</p>
  </section>

  <section class="policy" style="top:790px">
    <h2>Students with Disabilities</h2>
    <p>The Americans with Disabilities Act requires an institution of higher education to provide reasonable accommodation to individuals with a documented disability provided that the accommodation does not create a significant financial or disruptive detriment to the program.&nbsp; Reasonable accommodation can include use of aids, changing of testing or altering coursework, and ease of access to facility.</p>
  </section>

  <section class="policy" style="top:924px">
    <h2>Harrassment &amp; Discrimination Policy</h2>
    <p>Redwell Institute is committed to maintaining a fair and respectful learning environment for all.&nbsp; In accordance with federal and state law, Board of Regents’ policy, and University policy, the University prohibits any faculty members, staff, students, independent contractors, volunteers or visitors to campus from harassing and/or discriminating against any other member of the University due to the person's race, sex (including sexual harassment), sexual orientation, ethnicity or national origin, religion, age, disabled status, or status as a disabled veteran.&nbsp; Incidents of harassment and discrimination will be met with appropriate disciplinary action, up to and including dismissal from the University.</p>
  </section>

  <div class="footer-rule"></div>
  <div class="folio">21::: REDWELL INSTITUTE</div>
</div>
</body>
</html>
```